Local Flower Farm Needs Business Card Design

I need business cards designed for a flower farm based in Eudora, Kansas.
Business Info:
We are a local cut flower farm located in Eudora, Kansas, founded by Corinne Haldwick. What started as a passion for agriculture and search for more joy in daily life has blossomed into a small business dedicated to providing the community with beautiful, fresh, and sustainable flowers. We specialize in local, seasonal blooms, ensuring that every petal reflects the care and dedication we pour into our craft. Our mission is to deliver the highest quality flowers directly to our customers through local farmers markets and to florists who share our commitment to sustainability. Join us in celebrating the beauty of nature, one bloom at a time!
Contact Details:
Corinne Haldwick
Owner
Phone 913-555-0147
Facebook: Rosalind Thorpe Gardens
Instagram: @RosalindThorpeGardens
Website: RosalindThorpeGardens.example
Target Market(s)
Wholesale to Florists and Direct to Consumer via Farmers Market
Industry/Entity Type
Florist, Farm
Contact Information for Business Card
Name, Contact Info, Logo
Look and feel
Each slider illustrates characteristics of the customer's brand and the style your logo design should communicate.

```html
<!DOCTYPE html>
<html lang="en">
<head>
<meta charset="utf-8">
<title>Rosalind Thorpe Gardens – Business Card</title>
<link href="https://fonts.googleapis.com/css2?family=Tinos:wght@400;700&display=swap" rel="stylesheet">
<style>
  :root {
    --page-bg: #dfe3e5;
    --brand-teal: #0b2830;
    --card-white: #ffffff;
    --ink: #111111;
    --rule: #555555;
  }
  html, body {
    margin: 0;
    padding: 0;
    width: 1200px;
    height: 960px;
    overflow: hidden;
    background: var(--page-bg);
    font-family: "Tinos", "Times New Roman", serif;
  }
  .canvas {
    position: relative;
    width: 1200px;
    height: 960px;
  }
  .card {
    position: absolute;
    left: 247px;
    width: 706px;
    height: 402px;
    box-sizing: border-box;
  }
  .card--front {
    top: 60px;
    background: var(--brand-teal);
  }
  .card--back {
    top: 500px;
    background: var(--card-white);
  }
  .brand-mark {
    position: absolute;
    border-radius: 50%;
    display: flex;
    align-items: center;
    justify-content: center;
    text-align: center;
    box-sizing: border-box;
    font-family: "Tinos", "Times New Roman", serif;
    font-weight: 400;
    text-transform: uppercase;
    letter-spacing: 0.14em;
    line-height: 1.35;
  }
  .card--front .brand-mark {
    left: 218px;
    top: 66px;
    width: 270px;
    height: 270px;
    border: 1px solid var(--card-white);
    color: var(--card-white);
    font-size: 22px;
  }
  .card--back .brand-mark {
    left: 72px;
    top: 89px;
    width: 222px;
    height: 222px;
    border: 1px solid var(--brand-teal);
    color: var(--brand-teal);
    font-size: 18px;
  }
  .divider {
    position: absolute;
    left: 350px;
    top: 52px;
    width: 1px;
    height: 297px;
    background: var(--rule);
  }
  .contact-block {
    position: absolute;
    left: 392px;
    top: 108px;
    color: var(--ink);
  }
  .person-name {
    margin: 0;
    font-size: 34px;
    font-weight: 700;
    letter-spacing: 0.01em;
    line-height: 1;
  }
  .person-role {
    margin: 3px 0 0;
    font-size: 17px;
    font-weight: 400;
  }
  .contact-list {
    list-style: none;
    margin: 48px 0 0;
    padding: 0;
  }
  .contact-item {
    display: flex;
    align-items: center;
    height: 24px;
    font-size: 18px;
    letter-spacing: 0.02em;
  }
  .contact-icon {
    width: 16px;
    height: 16px;
    margin-right: 9px;
    flex: none;
  }
</style>
</head>
<body>
<main class="canvas">
  <section class="card card--front" aria-label="Card front">
    <div class="brand-mark">Rosalind<br>Thorpe<br>Gardens</div>
  </section>

  <section class="card card--back" aria-label="Card back">
    <div class="brand-mark">Rosalind<br>Thorpe<br>Gardens</div>
    <div class="divider"></div>
    <div class="contact-block">
      <h1 class="person-name">Corinne Haldwick</h1>
      <p class="person-role">Owner</p>
      <ul class="contact-list">
        <li class="contact-item">
          <svg class="contact-icon" viewBox="0 0 16 16" aria-hidden="true">
            <path d="M3.5 1.5l2.5 0.5 1 3-1.6 1.2a8 8 0 0 0 4.4 4.4L11 9l3 1 0.5 2.5-2 2A11 11 0 0 1 1.5 3.5z" fill="var(--brand-teal)"/>
          </svg>
          913-555-0147
        </li>
        <li class="contact-item">
          <svg class="contact-icon" viewBox="0 0 16 16" aria-hidden="true">
            <circle cx="8" cy="8" r="7.5" fill="var(--brand-teal)"/>
          </svg>
          Rosalind Thorpe Gardens
        </li>
        <li class="contact-item">
          <svg class="contact-icon" viewBox="0 0 16 16" aria-hidden="true">
            <rect x="1" y="1" width="14" height="14" rx="3" fill="none" stroke="var(--brand-teal)" stroke-width="2"/>
          </svg>
          @RosalindThorpeGardens
        </li>
        <li class="contact-item">
          <svg class="contact-icon" viewBox="0 0 16 16" aria-hidden="true">
            <circle cx="8" cy="8" r="7" fill="none" stroke="var(--brand-teal)" stroke-width="1.5"/>
            <ellipse cx="8" cy="8" rx="3" ry="7" fill="none" stroke="var(--brand-teal)" stroke-width="1.2"/>
            <line x1="1" y1="8" x2="15" y2="8" stroke="var(--brand-teal)" stroke-width="1.2"/>
          </svg>
          RosalindThorpeGardens.example
        </li>
      </ul>
    </div>
  </section>
</main>
</body>
</html>
```